Letter and Envelope Design For Harborline Realty

Please design a letter and an envelope incorporating our logo (See Attached). We are also launched a business card contest. Since we want them to match, please feel free to submit a design for both the business card and also the letter design and envelope.

Requirements
Must have
• The envelope, the letter and the business cards must match somehow connecting the designs. We want them to have something that holds them together besides the logo.

```html
<!DOCTYPE html>
<html lang="en">
<head>
<meta charset="utf-8">
<title>Harborline Realty Stationery</title>
<link rel="stylesheet" href="https://fonts.googleapis.com/css2?family=Montserrat:wght@500;600&family=Source+Sans+3:wght@400;600;700&display=swap">
<style>
  :root {
    --brand-blue: #0b1a8c;
    --brand-grey: #58595b;
    --ink: #3f3f3f;
    --paper: #ffffff;
    --stage: #e4e4e4;
    --card-dark: #1d1d1e;
  }
  * { margin: 0; padding: 0; box-sizing: border-box; }
  html, body { width: 1200px; height: 825px; overflow: hidden; }
  body {
    position: relative;
    background: var(--stage);
    font-family: "Source Sans 3", Arial, sans-serif;
    color: var(--ink);
  }
  .sheet {
    position: absolute;
    background: var(--paper);
    overflow: hidden;
    border-bottom: 3px solid var(--brand-blue);
  }
  .header-art {
    position: absolute;
    top: 0;
    right: 0;
    background: linear-gradient(90deg, rgba(11,26,140,0) 0%, rgba(11,26,140,0.55) 55%, var(--brand-blue) 85%, var(--brand-grey) 100%);
  }
  .brand { position: absolute; text-align: center; }
  .brand-ring {
    display: block;
    margin: 0 auto;
    border: 2.5px solid var(--brand-blue);
    border-radius: 50%;
    background: var(--paper);
  }
  .brand-name {
    display: block;
    font-family: "Montserrat", Arial, sans-serif;
    font-weight: 600;
    color: var(--brand-blue);
    letter-spacing: 0.14em;
    line-height: 1.2;
    white-space: nowrap;
  }
  .contact {
    position: absolute;
    text-align: right;
    font-size: 7.6px;
    line-height: 9.6px;
    color: var(--ink);
    list-style: none;
  }
  .contact li::after {
    content: "";
    display: inline-block;
    width: 4px; height: 4px;
    margin-left: 3px;
    background: var(--brand-blue);
    border-radius: 50%;
    vertical-align: middle;
  }
  .address {
    position: absolute;
    font-size: 7.6px;
    line-height: 9px;
    color: var(--ink);
    display: flex;
    align-items: flex-start;
    gap: 3px;
  }
  .address svg { flex: none; margin-top: 1px; }

  /* Letterhead */
  .letter { left: 80px; top: 84px; width: 463px; height: 655px; }
  .letter .header-art { left: 190px; height: 58px; }
  .letter .brand { left: 54px; top: 16px; }
  .letter .brand-ring { width: 48px; height: 48px; }
  .letter .brand-name { font-size: 11.5px; margin-top: 6px; }
  .letter .contact { right: 42px; top: 68px; }
  .salutation {
    position: absolute; left: 42px; top: 165px;
    font-family: Arial, sans-serif; font-weight: 700; font-size: 11.5px; color: #222;
  }
  .letter-body { position: absolute; left: 42px; top: 192px; width: 379px; }
  .letter-body p {
    font-size: 9.6px; line-height: 12.1px; text-align: justify; margin-bottom: 12px;
  }
  .signature {
    position: absolute; left: 42px; top: 470px; width: 74px; height: 36px;
    background: linear-gradient(90deg, #f6f6f6, #eeeeee);
    border-radius: 4px;
  }
  .letter .address { left: 44px; top: 637px; }

  /* Envelope front */
  .envelope-front { left: 584px; top: 102px; width: 532px; height: 232px; }
  .envelope-front .header-art { left: 200px; height: 60px; }
  .envelope-front .brand { left: 70px; top: 20px; }
  .envelope-front .brand-ring { width: 48px; height: 48px; }
  .envelope-front .brand-name { font-size: 11.5px; margin-top: 6px; }
  .envelope-front .contact { right: 34px; top: 70px; }
  .envelope-front .address { left: 46px; top: 213px; }

  /* Envelope back */
  .envelope-back {
    position: absolute; left: 584px; top: 361px; width: 532px; height: 231px;
    background: var(--paper);
  }
  .envelope-back .flap { position: absolute; left: 0; top: 0; width: 100%; height: 60px; }

  /* Business cards */
  .card-front { left: 632px; top: 628px; width: 196px; height: 111px; border-bottom-width: 2px; }
  .card-front .header-art { left: 80px; height: 26px; }
  .card-front .brand { left: 12px; top: 6px; }
  .card-front .brand-ring { width: 22px; height: 22px; border-width: 1.5px; }
  .card-front .brand-name { font-size: 6.4px; margin-top: 3px; }
  .card-person { position: absolute; right: 12px; top: 33px; text-align: right; }
  .card-person .person-name { display: block; font-size: 6px; font-weight: 700; color: var(--brand-blue); }
  .card-person .person-role { display: block; font-size: 5px; color: var(--ink); }
  .card-front .contact { right: 12px; top: 50px; font-size: 5px; line-height: 6.6px; }
  .card-front .contact li::after { width: 3px; height: 3px; }
  .card-front .address { left: 12px; top: 92px; font-size: 5px; line-height: 6px; }

  .card-back {
    position: absolute; left: 854px; top: 628px; width: 196px; height: 111px;
    background: var(--card-dark);
  }
  .card-back .brand { left: 0; right: 0; top: 22px; }
  .card-back .brand-ring { width: 30px; height: 30px; border: 2px solid var(--paper); background: transparent; }
  .card-back .brand-name { font-size: 8.4px; margin-top: 5px; color: var(--paper); }
</style>
</head>
<body>

<!-- Letterhead -->
<section class="sheet letter">
  <div class="header-art" role="img" aria-label="Decorative blue and grey header band"></div>
  <div class="brand">
    <span class="brand-ring"></span>
    <span class="brand-name">HARBORLINE<br>REALTY</span>
  </div>
  <ul class="contact">
    <li>555-014-2270</li>
    <li>info@harborlinerealty.com</li>
    <li>www.harborlinerealty.com</li>
  </ul>
  <p class="salutation">Dear Mr. Carter,</p>
  <div class="letter-body">
    <p>Lorem Ipsum is simply dummy text of the printing and typesetting industry. Lorem Ipsum has been the industry's standard dummy text ever since the 1500s, when an unknown printer took a galley of type and scrambled it to make a type specimen book. It has survived not only five centuries, but also the leap into electronic typesetting, remaining essentially unchanged.</p>
    <p>The standard chunk of Lorem Ipsum used since the 1500s is reproduced below for those interested. Sections 1.10.32 and 1.10.33 from "de Finibus Bonorum et Malorum" by Marcus Vellan are also reproduced in their exact original form, accompanied by English versions from the 1914 translation by J. Tolland</p>
    <p>Lorem Ipsum is simply dummy text of the printing and typesetting industry. Lorem Ipsum has been the industry's standard dummy text ever since the 1500s, when an unknown printer took a galley of type and scrambled it to make a type specimen book. It has survived not only five centuries, but also the leap into electronic typesetting, remaining essentially unchanged. It was popularised in the</p>
    <p>The standard chunk of Lorem Ipsum used since the 1500s is reproduced below for those interested. Sections 1.10.32 and 1.10.33 from "de Finibus Bonorum et Malorum" by Marcus Vellan are also reproduced in their exact original form, accompanied by English versions from the 1914 translation by J. Tolland</p>
  </div>
  <div class="signature" role="img" aria-label="Handwritten signature"></div>
  <p class="address">
    <svg width="7" height="9" viewBox="0 0 7 9" aria-hidden="true"><path fill="var(--brand-blue)" d="M3.5,0 A3.5,3.5 0 0 1 7,3.5 C7,6 3.5,9 3.5,9 C3.5,9 0,6 0,3.5 A3.5,3.5 0 0 1 3.5,0 Z M3.5,2 A1.5,1.5 0 1 0 3.5,5 A1.5,1.5 0 1 0 3.5,2 Z"/></svg>
    <span>Po. box 201, Street Name, City Name, Zip Code - 00000</span>
  </p>
</section>

<!-- Envelope front -->
<section class="sheet envelope-front">
  <div class="header-art" role="img" aria-label="Decorative blue header band"></div>
  <div class="brand">
    <span class="brand-ring"></span>
    <span class="brand-name">HARBORLINE<br>REALTY</span>
  </div>
  <ul class="contact">
    <li>555-014-2270</li>
    <li>info@harborlinerealty.com</li>
    <li>www.harborlinerealty.com</li>
  </ul>
  <p class="address">
    <svg width="7" height="9" viewBox="0 0 7 9" aria-hidden="true"><path fill="var(--brand-blue)" d="M3.5,0 A3.5,3.5 0 0 1 7,3.5 C7,6 3.5,9 3.5,9 C3.5,9 0,6 0,3.5 A3.5,3.5 0 0 1 3.5,0 Z M3.5,2 A1.5,1.5 0 1 0 3.5,5 A1.5,1.5 0 1 0 3.5,2 Z"/></svg>
    <span>Po. box 201, Street Name, City Name, Zip Code - 00000</span>
  </p>
</section>

<!-- Envelope back -->
<section class="envelope-back">
  <svg class="flap" viewBox="0 0 532 60" preserveAspectRatio="none" aria-hidden="true">
    <path fill="none" stroke="#ececec" stroke-width="1.5" d="M0,40 C2,54 12,56 24,56 L508,56 C520,56 530,54 532,40"/>
  </svg>
</section>

<!-- Business card front -->
<section class="sheet card-front">
  <div class="header-art" role="img" aria-label="Decorative blue and grey header band"></div>
  <div class="brand">
    <span class="brand-ring"></span>
    <span class="brand-name">HARBORLINE<br>REALTY</span>
  </div>
  <p class="card-person">
    <span class="person-name">Dr. Elena M. Hart</span>
    <span class="person-role">President</span>
  </p>
  <ul class="contact">
    <li>555-014-2270</li>
    <li>info@harborlinerealty.com</li>
    <li>www.harborlinerealty.com</li>
  </ul>
  <p class="address">
    <svg width="5" height="7" viewBox="0 0 7 9" aria-hidden="true"><path fill="var(--brand-blue)" d="M3.5,0 A3.5,3.5 0 0 1 7,3.5 C7,6 3.5,9 3.5,9 C3.5,9 0,6 0,3.5 A3.5,3.5 0 0 1 3.5,0 Z M3.5,2 A1.5,1.5 0 1 0 3.5,5 A1.5,1.5 0 1 0 3.5,2 Z"/></svg>
    <span>Po. box 201, Street Name,<br>City Name, Zip Code - 00000</span>
  </p>
</section>

<!-- Business card back -->
<section class="card-back">
  <div class="brand">
    <span class="brand-ring"></span>
    <span class="brand-name">HARBORLINE<br>REALTY</span>
  </div>
</section>

</body>
</html>
```